Brochure Brightwell Hearth Partners

Brochure 12 x 9 tri fold with insert/ Rack card 9x4. Brightwell Hearth Partners 318 Corvane Street Easton, MD 21629410-822-2207AgingAtHomeSolution.com Tag: Devoted to Thoughtful Household Support.
What we do: Home care agency that services higher end Clients Artsy area on the water. Taking care of seniors in their home.

Our story: Opening Brightwell Hearth Partners, Inc. is my way of making a difference in an industry that is dominated by franchises that often have their policies dictated by corporate policy-makers who are unfamiliar with local customs. My goal is to raise the level of non-medical home health care in our area by providing additional, customized training, higher wages for our care-partners and an inclusive workforce in the decision-making process when developing customized care planning for our clients. Through collaboration with the client, their family and care-partners I have learned what issues, concerns and disappointments may arise which enables me to provide a more defined solution for those in need.My goal of providing superior training required locating a nationally recognized curriculum that would serve our clients’ needs. I found the perfect fit with Norla Vance’s, Kindred Pathway Method™ and her Shifting Stones Series™. These programs provide our care-partners with the tools needed to handle the challenges of natural aging and living with Dementia. I was so impressed with these programs, I became a Certified Independent Trainer; one of five in the State of Maryland. There is a bonus for our care-partners who are required to maintain Continuing Education Units - these programs qualify for credit! Improving our industry by providing exemplary care-partners is my goal!I look forward to assisting you with your needs! Dana Prewitt Owner

Services: Companion Care Service - Conversation and Companionship , Meal Preparation, Light House Keeping, Errand Service ,Grocery Shopping ,Incidental Transportation, Laundry & Linen Washing, Medication Reminders, Recreational Activities ,
Personal Care Services: Bathing ,Mobility ,Transferring & Positioning ,Incontinence Care ,Oral Hygiene ,Feeding, Toileting ,Grooming & Dressing, Special Diet Preparation.

Our Commitment to You: Extensive Care-Partner Education - We provide, in addition to state mandated training, eight additional hours of hands-on Dementia training from a Certified, Independent Instructor on the “Kindred Pathway Method” by Norla Vance, a nationally recognized instructor on aging.

Nutrition/Local Chef Inspired Training ;We provide six, two-hour food preparation sessions for our care-partners using local chefs, their recipes and locally grown food.

Meaningful & Engaging Activities - We provide a monthly list with local activities to our care-partners based on our client’s interest and capabilities. Focusing on what our client loved to do in the past.

Home Solutions When Needed; We provide management services to help keep our clients in their homes by working with current contractors or locating new ones to properly maintain a safe-living environment.

About owner: Dana Prewitt, owner of Brightwell Hearth Partners, has earned her certification as an Independent Trainer in the Kindred Pathway; Method (KPM) by Norla Vance, a nationally recognized instructor on natural aging and aging with Dementia. Dana is one of five certified independent trainers in the state of Maryland. All staff will have eight hours of hands on Dementia Kindred Pathway Method training.

On the insert 11x 4.25 want the top to be sticking out of the tri -fold "Dementia Experts . I would like to have shades of each STONE as it progresses
The Shifting STONES(R): The STONES model recognizes the dynamic nature of the human brain and its abilities. Unlike other cognitive models, it acknowledges that everyone’s abilities can change in a moment. Modifying environments, situations, interactions, and expectations will create either supportive positive opportunities or result in distress and a sense of failure. Just as gemstones need different settings and care to show their best characteristics, so do people. Rather than focusing on a person’s loss when there is brain change, seeing individuals as precious, unique, and capable encourages a care partnership and is the core of this model. Providing supportive settings for everyone, including care providers, allows them to use what they have to be their best. The STONES® advocate that everyone living with brain change when given the opportunity will shine. Norla Vance and Kindred Pathway Method

Sapphire ~ True Blue ~ Optimal Cognition, Healthy Brain•
True to self: personal preferences remain basically the same
• Can be flexible in thinking and appreciate multiple perspectives
• Stress/pain/fatigue may trigger Diamond state: back to Sapphire with relief
• Able to suppress and filter personal reactions: chooses effective responses
• Selects from options and can make informed decisions
• Processes well and able to successfully transition
• Aging doesn’t change ability: processing slows, more effort/time/practice needed
My brain is healthy - true blue. If I am aging normally or distressed, it may be hard for me to find words. I can describe what I am thinking so you understand. I may talk to myself because I am giving myself cues and prompts. I can learn new things and change habits, but it takes time and effort. Honoring my choices and preferences, when possible, is important. I need more time to make decisions. Give me the details and let me think about it before you need an answer. I am able to remember plans and information but supports are helpful. I may like specific prompts such as notes, calendars, and reminder calls. Health changes in vision, hearing, balance, coordination, depression, anxiety, pain, or medication may impact my behavior, but my cognitive abilities remain the same.

Diamond ~ Clear and Sharp ~ Routines and Rituals Rule
• Displays many facets: behavior and perspective can shift dramatically
• Prefers the familiar and may resist change: challenged by transitions
• More rigid and self-focused; sees wants as needs, when stressed
• Personal likes/dislikes in relationships/space/belongings etc, become more intense
• Reacts to changes in environment; benefits from familiar; functional/forgiving
• Needs repetition and time to absorb new/different information or routines
• Trusted authority figures can help: reacts better when respect is mutual
My overall cognition is clear and sharp. When happy and supported, I am capable and shine in my abilities. When distressed, I can be cutting and rigid and may see help as a threat. I have trouble seeing other points of view and may become less aware of boundaries or more possessive about my relationships, personal space, and belongings. I have many facets so people see me differently depending on the situation. This can cause conflict among my family, friends, or care team as it’s hard to tell if I am choosing my behavior or truly have limits in my ability. I can socially engage and have good cover skills. People will vary in their awareness of what is happening to me. I want to keep habits and environments as they have always been, even if they are problematic for me or others. I am often focused on the past, personal values, or finances. I will need help to make changes in my life; it’s hard for me. I can be in a Diamond state for reasons other than dementia.

Emerald ~ Green and On the Go With a Purpose ~ Naturally Flawed
• Sees self as able and independent, with limited awareness of changes in ability
• Lives in moments of clarity mixed with periods of loss in logic/reason/perspective
• Understanding and use of language change: vague words and many repeats
• Cues and support help when getting to/from places and doing daily routines
• Awareness of time, place, and situation will not always match current reality
• Strong emotional reactions are triggered by fears, desires, or unmet needs
Needs to know what comes next: seeks guidance and assistance to fill the day
I am flawed; it is part of being a natural emerald. I tend to be focused on what I want or need in this moment and may not be aware of my own safety or changing abilities. I can chat socially, but I typically miss one out of every four words and cannot accurately follow the meaning of longer conversations. I won’t remember the details of our time together, but I will remember how your body language and tone of voice made me feel. I may hide or misplace things and believe someone has taken them. My brain will make up information to fill in the blanks, which makes you think I am lying. If you try to correct me or argue, I may become resentful or suspicious of you. I am not always rational, but I don’t want to be made to feel incompetent. My brain plays tricks on me, taking me to different times and places in my life. When I am struggling, I may tell you, “I want to go home.” To provide the help and assistance I need, you must go with my flow, use a positive, partnered approach, and modify my environment.

Amber ~ Caught in a Moment of Time ~ Caution Required
• Focused on sensation: seeks to satisfy desires and tries to avoid what is disliked
•Environment can drive actions and reactions without awareness of safety
• Visual abilities are limited: focus is on pieces or parts, not the whole picture
• What happens to or around an Amber, may cause strong and surprising reactions
• Enters others’ space and crosses boundaries attempting to meet own needs
• Has periods of intense activity: may be very curious or repetitive with objects or actions
• Care is refused or seen as threatening, due to differences in perspective and ability.
Like a particle trapped in an amber, I am caught in a moment of time. It may surprise you to see how I take in the world around me. I may not know you or see you as a whole person. I react to you based on how you look, sound, move, smell, and respond to me. I like to do simple tasks over and over and may need to repeatedly move and touch, smell, taste, take or tear items apart. While it may exhaust or frustrate you, it soothes me. I don’t recognize danger; you will have to safeguard my environment. I’m intolerant to discomfort because my mouth, hands, feet, and genitalia are highly sensitive due to changes in my nervous system. Therefore, activities like eating, taking medication, mouth care, bathing, dressing, and toileting may distress me. Please notice my reaction and stop if I am resisting. I can’t help myself and one or both of us may get hurt emotionally and/or physically. If this happens, wait a few minutes, connect with me, and try a different approach; possibly substituting one area of focus for another.

Ruby ~ Deep and Strong in Color ~ Others Stop Seeing What is Possible
• Makes use of rhythm: can usually sing, hum, pray, sway, rock, clap, and dance
• When moving can’t stop; when stopped can’t get moving: needs guidance and help
• Big, strong movements are possible, while skilled abilities are being lost
• Danger exists due to limited abilities combined with automatic actions or reactions
• Tends to miss subtle hints, but gets magnified facial expressions and voice rhythms
• Can mimic actions or motions, but will struggle to understand instructions/gestures
• Able to pick up and hold objects, and yet not know what to do with them
As the deep red of a ruby masks detail, my obvious losses make my remaining abilities harder to notice. Although my fine motor skills have become very limited, remember that I am able to move and do simple things with my hands. You will need to anticipate, identify, and respond to all of my needs, even though I may not be aware of them. Plan to create a supportive environment, help with the details of care, and structure my day. Just as a crossing guard directs traffic, you will need to guide my movements and transitions. I can rarely stop or start on my own and switching gears is a challenge. Move with me first, then use your body to show me what you want me to do next, going one step at a time. Palm-beneath-Palm™ assistance helps me to feel safe and secure and to know what to do. Danger is part of my life, due to losses in visual skills, chewing abilities, balance, and coordination. You can reduce the risks to me, but not eliminate them. I can still have moments of joy when you are able to provide what gives me pleasure.

Pearl ~ Hidden Within a Shell ~ Beautiful Moments to Behold
• Will frequently recognize familiar touches, voices, faces, aromas, and tastes• Personhood survives, although all other capabilities are minimal
• Understanding input takes time: go slow and simplify for success
• In care, first get connected by offering comfort then use careful and caring touch
• Changes in the body are profound: weight loss, immobility, systems are failing
• As protective reflexes are lost, breathing, swallowing, and moving will be difficult
Care partners benefit from learning the art of letting go rather than simply giving up
While hidden like a pearl in an oyster shell, I will still have moments when I become alert and responsive. I am near the end of my life. Moments of connection create a sense of wholeness and value between us. Use our time together not just to provide care, but to comfort and connect with me. To help me complete life well, it’s important to honor my personhood when making medical or care decisions; please don’t talk about me as though I am not still here. I respond best to familiar voices and gentle rhythmic movements. I am ruled by reflexes and will startle easily. My brain is losing its ability to control and heal my body. Be prepared to see me having difficulty breathing or swallowing. My body may no longer desire food and drink as I prepare to leave this life. I may not be able to stop living without permission from you. Your greatest gift at this time in my life is to let me know that it is okay to go.

Target Market(s)

Children of seniors, seniors , rehabilitation centers

Requirements
Must have
• Nice photos of Seniors that are happy doing thing they like to do with help (Caregivers)
• Upbeat . Positive
Nice to have
• Processional looking - but very personal, we are taking care of their love ones
Should not have
• Not to feel like a cold hospital or end of life

```html
<!DOCTYPE html>
<html lang="en">
<head>
<meta charset="utf-8">
<title>Brightwell Hearth Partners – Tri-fold Brochure</title>
<link href="https://fonts.googleapis.com/css2?family=Montserrat:wght@400;600;700&family=Open+Sans:ital,wght@0,400;0,600;1,400&family=Roboto+Condensed:ital,wght@0,400;0,700;1,400&family=Roboto:ital,wght@0,700;1,400&family=Oswald:wght@600&display=swap" rel="stylesheet">
<style>
:root{
  --stage:#6f6f6f;
  --paper:#ffffff;
  --navy:#0f3a78;
  --navy-deep:#0b2b5e;
  --teal:#1a6f9e;
  --ink:#3a3a3a;
  --band:#404040;
  --sky:#6cc4ee;
  --sapphire:#1e2a8f;
  --diamond:#6d6d6d;
  --emerald:#1c6b2b;
  --amber:#c8650a;
  --ruby:#d0141b;
  --pearl:#a5622a;
  --tone-sapphire:#3b3fb8;
  --tone-diamond:#c9c9c9;
  --tone-emerald:#2f9a2c;
  --tone-amber:#eaa019;
  --tone-ruby:#c4161c;
  --tone-pearl:#d9bd9c;
}
*{box-sizing:border-box;margin:0;padding:0}
html,body{width:824px;height:1200px;overflow:hidden}
body{background:radial-gradient(circle at 50% 45%,#8a8a8a,var(--stage));font-family:'Open Sans',sans-serif;color:var(--ink);position:relative}
.spread{position:absolute;left:48px;width:732px;height:548px;background:var(--paper);box-shadow:0 6px 14px rgba(0,0,0,.45);overflow:hidden}
.spread--outside{top:22px}
.spread--inside{top:622px}
.fold{position:absolute;top:0;bottom:0;width:244px}
.fold--mid{left:244px;background:linear-gradient(90deg,#eceef0 0,#fff 18px,#fff 226px,#f1f1f1 100%)}
.fold--right{left:488px;background:linear-gradient(90deg,#eceef0 0,#fff 16px)}
.abs{position:absolute}

/* outside – services fold */
.tag{background:var(--navy-deep);color:#fff;font:700 8px 'Montserrat',sans-serif;padding:1px 4px;border-radius:3px;letter-spacing:.3px}
.h-sub{font:700 7.6px 'Montserrat',sans-serif;color:var(--navy)}
.h-sec{font:600 7.6px 'Montserrat',sans-serif;color:var(--navy)}
.h-main{font:700 8.4px 'Montserrat',sans-serif;color:var(--navy-deep)}
.svc-list{list-style:none;display:grid;grid-template-columns:117px 100px;row-gap:3px;font:400 6.2px 'Montserrat',sans-serif;color:#444}
.svc-list li{position:relative;padding-left:7px;line-height:9px;white-space:nowrap}
.svc-list li::before{content:"";position:absolute;left:0;top:3px;width:3.4px;height:3.4px;border-radius:50%;border:1.1px solid var(--navy)}
.body-copy{font:400 6.2px/8.5px 'Montserrat',sans-serif;color:#444;text-align:justify}
.photo{border-radius:3px}

/* story fold */
.story-col{position:absolute;left:266px;top:18px;width:199px}
.story-h{font:700 12px 'Montserrat',sans-serif;color:var(--navy-deep);letter-spacing:.4px;margin-bottom:4px}
.story{font:400 6.3px/8.6px 'Open Sans',sans-serif;color:#444;text-align:justify;margin-bottom:7px}
.sign{font:italic 400 6.3px/8.5px 'Open Sans',sans-serif;color:#333;margin-top:10px}
.role{font:400 6.3px/8.5px 'Open Sans',sans-serif;color:#444}
.brand{font:400 15px 'Montserrat',sans-serif;color:var(--teal);line-height:18px;text-align:center}
.contact{font:400 9px/11.5px 'Montserrat',sans-serif;color:#333}
.contact strong{font-weight:600;color:var(--navy)}
.icon{position:absolute;width:8px;height:8px}

/* cover fold */
.cover-h1{font:600 17px/19px 'Oswald',sans-serif;color:var(--navy-deep);text-align:center;letter-spacing:.2px}
.cover-h2{font:600 22px/24px 'Oswald',sans-serif;color:var(--teal);text-align:center;letter-spacing:.4px}
.pill{background:var(--navy-deep);color:#fff;border-radius:9px;font:400 7.2px/17px 'Montserrat',sans-serif;text-align:center}

/* inside – stones insert */
.band{position:absolute;left:0;top:0;width:732px;height:101px;background:var(--band)}
.band-title{font:700 14px 'Montserrat',sans-serif;color:var(--sky);letter-spacing:.2px}
.band-sub{font:600 7.5px 'Open Sans',sans-serif;color:#fff}
.band-copy{font:italic 400 6px/8.5px 'Open Sans',sans-serif;color:#eee;text-align:justify}
.stones-mark{border-radius:50%;background:#fff;display:flex;align-items:center;justify-content:center;font:700 9px 'Montserrat',sans-serif;color:var(--emerald)}
.stone-block{position:absolute;width:203px}
.stone-head{display:flex;align-items:center;gap:9px;height:34px;margin-bottom:5px}
.stone-swatch{flex:none;width:34px;height:34px;border-radius:4px}
.stone-name{font:700 10px 'Roboto',sans-serif;line-height:11px}
.stone-tag{font:italic 400 7.4px/8.6px 'Roboto',sans-serif;color:#333}
.traits{list-style:none;font:400 5.6px 'Roboto Condensed',sans-serif;color:#333;margin-bottom:5px}
.traits li{position:relative;padding-left:9px;line-height:11.4px;white-space:nowrap}
.traits li::before{content:"";position:absolute;left:0;top:3.5px;width:4px;height:4px;border-radius:50%;border:1.2px solid var(--navy)}
.traits b{font-weight:700}
.voice{font:italic 400 4.9px/6.9px 'Roboto Condensed',sans-serif;color:#444;text-align:justify}
.sapphire{color:var(--sapphire)}.diamond{color:var(--diamond)}.emerald{color:var(--emerald)}
.amber{color:var(--amber)}.ruby{color:var(--ruby)}.pearl{color:var(--pearl)}
</style>
</head>
<body>

<section class="spread spread--outside">
  <div class="fold fold--mid"></div>
  <div class="fold fold--right"></div>

  <div class="abs tag" style="left:21px;top:20px">SERVICES :</div>
  <div class="abs h-sub" style="left:21px;top:35px">Companion Care Service</div>
  <ul class="abs svc-list" style="left:21px;top:45px">
    <li>Conversation &amp; Companionship</li><li>Incidental Transportation</li>
    <li>Meal Preparation</li><li>Laundry &amp; Linen Washing</li>
    <li>Light House Keeping</li><li>Medication Reminders</li>
    <li>Errand Service</li><li>Recreational Activities</li>
    <li>Grocery Shopping</li><li></li>
  </ul>
  <div class="abs h-sub" style="left:21px;top:104px">Personal Care Services</div>
  <ul class="abs svc-list" style="left:21px;top:115px">
    <li>Bathing</li><li>Feeding</li>
    <li>Mobility</li><li>Toileting</li>
    <li>Transferring &amp; Positioning</li><li>Grooming &amp; Dressing</li>
    <li>Incontinence Care</li><li>Special Diet Preparation</li>
    <li>Oral Hygiene</li><li></li>
  </ul>
  <div class="abs h-main" style="left:21px;top:180px">Our Commitment to You:</div>
  <div class="abs h-sec" style="left:21px;top:192px">Extensive Care-Partner Education</div>
  <p class="abs body-copy" style="left:21px;top:204px;width:201px">We provide, in addition to state mandated training, eight additional hours of hands-on Dementia training from a Certified, Independent Instructor on the “Kindred Pathway Method” by Norla Vance, a nationally recognized instructor on aging.</p>

  <div class="abs h-sec" style="left:21px;top:247px">Nutrition/Local Chef Inspired Training</div>
  <p class="abs body-copy" style="left:21px;top:260px;width:103px">We provide six, two-hour food preparation sessions for our care-partners using local chefs, their recipes and locally grown food.</p>
  <div class="abs photo" role="img" aria-label="Photo of a hand holding fresh local vegetables in a garden" style="left:132px;top:262px;width:90px;height:45px;background:linear-gradient(135deg,#6f9a3a,#a9bb62 55%,#5c7a2e)"></div>

  <div class="abs h-sec" style="left:21px;top:316px">Meaningful &amp; Engaging Activities</div>
  <div class="abs photo" role="img" aria-label="Photo of a senior man painting at an easel" style="left:21px;top:328px;width:90px;height:45px;background:linear-gradient(120deg,#e9e2d6,#cdbba3 50%,#f1ece4)"></div>
  <p class="abs body-copy" style="left:120px;top:326px;width:102px">We provide a monthly list with local activities to our care-partners based on our client’s interest &amp; capabilities. Focusing on what our client loved to do in the past.</p>

  <div class="abs h-sec" style="left:21px;top:384px">Home Solutions When Needed</div>
  <p class="abs body-copy" style="left:21px;top:394px;width:103px">We provide management services to help keep our clients in their homes by working with current contractors or locating new ones to properly maintain a safe-living environment.</p>
  <div class="abs photo" role="img" aria-label="Photo of a contractor with a yellow hard hat and tool belt" style="left:132px;top:394px;width:90px;height:45px;background:linear-gradient(135deg,#8a5a3c,#c6a04e 55%,#7a5238)"></div>

  <div class="abs h-main" style="left:21px;top:455px">About owner:</div>
  <p class="abs body-copy" style="left:21px;top:468px;width:201px">Dana Prewitt, owner of Brightwell Hearth Partners, has earned her certification as an Independent Trainer in the Kindred Pathway® Method (KPM) by Norla Vance, a nationally recognized instructor on natural aging and aging with Dementia. Dana is one of five certified independent trainers in the state of Maryland. All staff will have eight hours of hands on Dementia Kindred Pathway Method training.</p>

  <div class="story-col">
    <h2 class="story-h">OUR STORY:</h2>
    <p class="story">Opening Brightwell Hearth Partners, Inc. is my way of making a difference in an industry that is dominated by franchises that often have their policies dictated by corporate policy-makers who are unfamiliar with local customs. My goal is to raise the level of non-medical home health care in our area by providing additional, customized training, higher wages for our care-partners and an inclusive workforce in the decision-making process when developing customized care planning for our clients. Through collaboration with the client, their family &amp; care-partners I have learned what issues, concerns and disappointments may arise which enables me to provide a more defined solution for those in need.</p>
    <p class="story" style="margin-bottom:0">My goal of providing superior training required locating a nationally recognized curriculum that would serve our clients’ needs. I found the perfect fit with Norla Vance’s, Kindred Pathway Method™ and her Shifting Stones Series™. These programs provide our care-partners with the tools needed to handle the challenges of natural aging &amp; living with Dementia. I was so impressed with these programs, I became a Certified Independent Trainer; one of five in the State of Maryland. There is a bonus for our care-partners who are required to maintain Continuing Education Units - these programs qualify for credit! Improving our industry by providing exemplary care-partners is my goal!<br>I look forward to assisting you with your needs!</p>
    <p class="sign">Dana Prewitt</p>
    <p class="role">Owner</p>
  </div>
  <div class="abs" role="img" aria-label="Faded photo of two clasped hands" style="left:300px;top:300px;width:160px;height:110px;background:radial-gradient(ellipse at 50% 55%,#dcdcdc,rgba(255,255,255,0) 70%)"></div>
  <svg class="abs" style="left:334px;top:296px" width="80" height="80" viewBox="0 0 80 80" role="img" aria-label="Trainer certification badge">
    <circle cx="40" cy="40" r="38" fill="#fff" stroke="var(--navy-deep)" stroke-width="4"/>
  </svg>
  <div class="abs brand" style="left:280px;top:412px;width:176px">Brightwell Hearth<br>Partners</div>
  <svg class="icon" style="left:287px;top:459px" viewBox="0 0 10 10" aria-hidden="true"><path d="M5 1 1 5h1.5v4h2.2V6.5h.6V9h2.2V5H9z" fill="var(--navy)"/></svg>
  <div class="abs contact" style="left:297px;top:455px"><strong>Brightwell Hearth Partners</strong><br>318 Corvane Street<br>Easton, MD 21774</div>
  <svg class="icon" style="left:287px;top:500px" viewBox="0 0 10 10" aria-hidden="true"><path d="M2.3 1.2 3.8 1l1 2.2-1 .8a5 5 0 0 0 2.2 2.2l.8-1 2.2 1-.2 1.5C8 8.6 7 9 6 8.6 3.9 7.8 2.2 6.1 1.4 4 1 3 1.4 2 2.3 1.2z" fill="var(--navy)"/></svg>
  <div class="abs contact" style="left:297px;top:496px;font-size:11px">410-555-0148</div>
  <svg class="icon" style="left:287px;top:517px" viewBox="0 0 10 10" aria-hidden="true"><circle cx="5" cy="5" r="4" fill="none" stroke="var(--navy)"/><path d="M1 5h8M5 1c-2 2.5-2 5.5 0 8M5 1c2 2.5 2 5.5 0 8" fill="none" stroke="var(--navy)" stroke-width=".7"/></svg>
  <div class="abs contact" style="left:297px;top:514px;font-size:7.6px">www.BrightwellHearthPartners.example</div>

  <div class="abs brand" style="left:500px;top:62px;width:220px;font-size:19px;line-height:22px">Brightwell Hearth<br>Partners</div>
  <div class="abs" role="img" aria-label="Photo of a smiling caregiver embracing a happy senior woman" style="left:490px;top:118px;width:242px;height:288px;background:linear-gradient(160deg,#f4f4f4 0,#e6d8cf 35%,#c99c86 55%,#eadfe6 80%,#f7f7f7)"></div>
  <div class="abs cover-h1" style="left:500px;top:427px;width:220px">DEVOTED TO THOUGHTFUL</div>
  <div class="abs cover-h2" style="left:500px;top:449px;width:220px">HOUSEHOLD SUPPORT</div>
  <div class="abs pill" style="left:536px;top:514px;width:148px">www.brightwellhearthpartners.example</div>
</section>

<section class="spread spread--inside">
  <div class="fold fold--mid" style="top:101px"></div>
  <div class="fold fold--right" style="top:101px"></div>
  <div class="band"></div>
  <div class="abs stones-mark" style="left:20px;top:18px;width:64px;height:64px">STONES</div>
  <div class="abs band-title" style="left:109px;top:17px">CAREGIVERS RECEIVE 8 HOURS’ DEMENTIA TRAINING</div>
  <div class="abs band-sub" style="left:109px;top:36px">Brain Change Model</div>
  <p class="abs band-copy" style="left:109px;top:47px;width:602px">The STONES® model recognizes the dynamic nature of the human brain &amp; its abilities. Unlike other cognitive models, it acknowledges that everyone’s abilities can change in a moment. Modifying environments, situations, interactions, and expectations will create either supportive positive opportunities or result in distress &amp; a sense of failure. Just as gemstones need different settings &amp; care to show their best characteristics, so do people. Rather than focusing on a person’s loss when there is brain change, seeing individuals as precious, unique, and capable encourages a care partnership and is the core of this model. Providing supportive settings for everyone, including care providers, allows them to use what they have to be their best. The STONES® advocate that everyone living with brain change when given the opportunity will shine.<br>- Norla Vance and Kindred Pathway Method Team</p>

  <div class="stone-block" style="left:21px;top:111px">
    <div class="stone-head"><div class="stone-swatch" role="img" aria-label="Sapphire gemstone photo" style="background:var(--tone-sapphire)"></div><div><div class="stone-name sapphire">SAPPHIRE ~</div><div class="stone-tag">True Blue ~ Optimal Cognition, Healthy Brain</div></div></div>
    <ul class="traits">
      <li><b>True to self:</b> personal preferences remain basically the same</li>
      <li>Can be flexible in thinking and appreciate multiple perspectives</li>
      <li><b>Stress/pain/fatigue may trigger Diamond state:</b> back to Sapphire with relief</li>
      <li>Able to suppress &amp; filter personal reactions: chooses effective responses</li>
      <li>Selects from options and can make informed decisions</li>
      <li>Processes well and able to successfully transition</li>
      <li><b>Aging doesn’t change ability:</b> processing slows, more effort/time/practice needed</li>
    </ul>
    <p class="voice"><b>My brain is healthy</b> - true blue. If I am aging normally or distressed, it may be hard for me to find words. I can describe what I am thinking so you understand. I may talk to myself because I am giving myself cues and prompts. I can learn new things and change habits, but it takes time and effort. Honoring my choices and preferences, when possible, is important. I need more time to make decisions. Give me the details and let me think about it before you need an answer. I am able to remember plans and information but supports are helpful. I may like specific prompts such as notes, calendars, and reminder calls. Health changes in vision, hearing, balance, coordination, depression, anxiety, pain, or medication may impact my behavior, but my cognitive abilities remain the same.</p>
  </div>

  <div class="stone-block" style="left:21px;top:322px">
    <div class="stone-head"><div class="stone-swatch" role="img" aria-label="Diamond gemstone photo" style="background:var(--tone-diamond)"></div><div><div class="stone-name diamond">DIAMOND ~</div><div class="stone-tag">Clear and Sharp ~ Routines and Rituals Rule</div></div></div>
    <ul class="traits">
      <li><b>Displays many facets:</b> behavior and perspective can shift dramatically</li>
      <li>Prefers the familiar and may resist change: challenged by transitions</li>
      <li>More rigid and self-focused; sees wants as needs, when stressed</li>
      <li>Personal likes/dislikes in relationships/space/belongings etc, become more intense</li>
      <li>Reacts to changes in environment; benefits from familiar; functional/forgiving</li>
      <li>Needs repetition and time to absorb new/different information or routines</li>
      <li><b>Trusted authority figures can help:</b> reacts better when respect is mutual</li>
    </ul>
    <p class="voice">My overall cognition is clear and sharp. When happy and supported, I am capable and shine in my abilities. When distressed, I can be cutting and rigid and may see help as a threat. I have trouble seeing other points of view and may become less aware of boundaries or more possessive about my relationships, personal space, and belongings. I have many facets so people see me differently depending on the situation. This can cause conflict among my family, friends, or care team as it’s hard to tell if I am choosing my behavior or truly have limits in my ability. I can socially engage and have good cover skills. People will vary in their awareness of what is happening to me. I want to keep habits and environments as they have always been, even if they are problematic for me or others. I am often focused on the past, personal values, or finances. I will need help to make changes in my life; it’s hard for me. I can be in a Diamond state for reasons other than dementia.</p>
  </div>

  <div class="stone-block" style="left:266px;top:111px">
    <div class="stone-head"><div class="stone-swatch" role="img" aria-label="Emerald gemstone photo" style="background:var(--tone-emerald)"></div><div><div class="stone-name emerald">EMERALD ~</div><div class="stone-tag">Green &amp; On the Go With a Purpose ~<br>Naturally Flawed</div></div></div>
    <ul class="traits">
      <li>Sees self as able and independent, with limited awareness of changes in ability</li>
      <li>Lives in moments of clarity mixed with periods of loss in logic/reason/perspective</li>
      <li>Understanding and use of language change: vague words and many repeats</li>
      <li>Cues and support help when getting to/from places and doing daily routines</li>
      <li>Awareness of time, place, and situation will not always match current reality</li>
      <li>Strong emotional reactions are triggered by fears, desires, or unmet needs</li>
    </ul>
    <p class="voice">Needs to know what comes next: seeks guidance and assistance to fill the day<br>I am flawed; it is part of being a natural emerald. I tend to be focused on what I want or need in this moment and may not be aware of my own safety or changing abilities. I can chat socially, but I typically miss one out of every four words and cannot accurately follow the meaning of longer conversations. I won’t remember the details of our time together, but I will remember how your body language and tone of voice made me feel. I may hide or misplace things and believe someone has taken them. My brain will make up information to fill in the blanks, which makes you think I am lying. If you try to correct me or argue, I may become resentful or suspicious of you. I am not always rational, but I don’t want to be made to feel incompetent. My brain plays tricks on me, taking me to different times &amp; places in my life. When I am struggling, I may tell you, “I want to go home.” To provide the help &amp; assistance I need, you must go with my flow, use a positive, partnered approach, &amp; modify my environment.</p>
  </div>

  <div class="stone-block" style="left:266px;top:322px">
    <div class="stone-head"><div class="stone-swatch" role="img" aria-label="Amber stone photo" style="background:var(--tone-amber)"></div><div><div class="stone-name amber">AMBER ~</div><div class="stone-tag">Caught in a Moment of Time ~ Caution Required</div></div></div>
    <ul class="traits">
      <li><b>Focused on sensation:</b> seeks to satisfy desires and tries to avoid what is disliked</li>
      <li>Environment can drive actions and reactions without awareness of safety</li>
      <li><b>Visual abilities are limited:</b> focus is on pieces or parts, not the whole picture</li>
      <li>What happens to or around an Amber, may cause strong and surprising reactions</li>
      <li>Enters others’ space and crosses boundaries attempting to meet own needs</li>
      <li><b>Has periods of intense activity:</b> may be very curious or repetitive with objects or actions</li>
      <li>Care is refused or seen as threatening, due to differences in perspective and ability</li>
    </ul>
    <p class="voice">Like a particle trapped in an amber, I am caught in a moment of time. It may surprise you to see how I take in the world around me. I may not know you or see you as a whole person. I react to you based on how you look, sound, move, smell, and respond to me. I like to do simple tasks over and over and may need to repeatedly move and touch, smell, taste, take or tear items apart. While it may exhaust or frustrate you, it soothes me. I don’t recognize danger; you will have to safeguard my environment. I’m intolerant to discomfort because my mouth, hands, feet, and genitalia are highly sensitive due to changes in my nervous system. Therefore, activities like eating, taking medication, mouth care, bathing, dressing, and toileting may distress me. Please notice my reaction &amp; stop if I am resisting. I can’t help myself &amp; one or both of us may get hurt emotionally &amp;/or physically. If this happens, wait a few minutes, connect with me, &amp; try a different approach; possibly substituting one area of focus for another.</p>
  </div>

  <div class="stone-block" style="left:509px;top:111px">
    <div class="stone-head"><div class="stone-swatch" role="img" aria-label="Ruby gemstone photo" style="background:var(--tone-ruby)"></div><div><div class="stone-name ruby">RUBY ~ <span class="stone-tag">Deep and Strong in Color ~</span></div><div class="stone-tag">Others Stop Seeing What is Possible</div></div></div>
    <ul class="traits">
      <li><b>Makes use of rhythm:</b> can usually sing, hum, pray, sway, rock, clap, and dance</li>
      <li>When moving can’t stop; when stopped can’t get moving: needs guidance &amp; help</li>
      <li>Big, strong movements are possible, while skilled abilities are being lost</li>
      <li>Danger exists due to limited abilities combined with automatic actions or reactions</li>
      <li>Tends to miss subtle hints, but gets magnified facial expressions and voice rhythms</li>
      <li>Can mimic actions or motions, but will struggle to understand instructions/gestures</li>
      <li>Able to pick up and hold objects, and yet not know what to do with them</li>
    </ul>
    <p class="voice">As the deep red of a ruby masks detail, my obvious losses make my remaining abilities harder to notice. Although my fine motor skills have become very limited, remember that I am able to move and do simple things with my hands. You will need to anticipate, identify, and respond to all of my needs, even though I may not be aware of them. Plan to create a supportive environment, help with the details of care, and structure my day. Just as a crossing guard directs traffic, you will need to guide my movements and transitions. I can rarely stop or start on my own and switching gears is a challenge. Move with me first, then use your body to show me what you want me to do next, going one step at a time. Palm-beneath-Palm™ assistance helps me to feel safe and secure and to know what to do. Danger is part of my life, due to losses in visual skills, chewing abilities, balance, and coordination. You can reduce the risks to me, but not eliminate them. I can still have moments of joy when you are able to provide what gives me pleasure.</p>
  </div>

  <div class="stone-block" style="left:509px;top:329px">
    <div class="stone-head"><div class="stone-swatch" role="img" aria-label="Pearl photo" style="background:var(--tone-pearl)"></div><div><div class="stone-name pearl">PEARL ~</div><div class="stone-tag">Hidden Within a Shell ~ Beautiful Moments<br>to Behold</div></div></div>
    <ul class="traits">
      <li>Will frequently recognize familiar touches, voices, faces, aromas, and tastes</li>
      <li>Personhood survives, although all other capabilities are minimal</li>
      <li>Understanding input takes time: go slow and simplify for success</li>
      <li>In care, first get connected by offering comfort then use careful and caring touch</li>
      <li>Changes in the body are profound: weight loss, immobility, systems are failing</li>
      <li>As protective reflexes are lost, breathing, swallowing, and moving will be difficult</li>
      <li>Care partners benefit from learning the art of letting go rather than simply giving up</li>
    </ul>
    <p class="voice">While hidden like a pearl in an oyster shell, I will still have moments when I become alert and responsive. I am near the end of my life. Moments of connection create a sense of wholeness and value between us. Use our time together not just to provide care, but to comfort and connect with me. To help me complete life well, it’s important to honor my personhood when making medical or care decisions; please don’t talk about me as though I am not still here. I respond best to familiar voices and gentle rhythmic movements. I am ruled by reflexes and will startle easily. My brain is losing its ability to control and heal my body. Be prepared to see me having difficulty breathing or swallowing. My body may no longer desire food and drink as I prepare to leave this life. I may not be able to stop living without permission from you. Your greatest gift at this time in my life is to let me know that it is okay to go.</p>
  </div>
</section>

</body>
</html>
```